Quillbrookes websites redesign

Www.quill-brookes.com needs to be redesigned along with updations. The incremental material will be provided for the updations. We are looking for complete redesign of the pages with the new content. The complete write up will be provided soon

Target Market(s)

Global

Coding

Coded - Design and coding required

Number of Pages Required

5+ page

Requirements
Must have
• A clean and slick design for the Consulting.
Should not have
• Too many pictures which reduces the speed of the site

```html
<!DOCTYPE html>
<html lang="en">
<head>
<meta charset="utf-8">
<title>Quillbrookes Consultancy</title>
<link href="https://fonts.googleapis.com/css2?family=Open+Sans:ital,wght@0,400;0,600;0,700;1,400&display=swap" rel="stylesheet">
<style>
:root{
  --blue:#3aa3cf;
  --blue-dark:#2f8fb9;
  --maroon:#6e1f22;
  --maroon-title:#7a2427;
  --ink:#2d3a48;
  --text:#666d75;
  --soft:#f2f3f5;
  --white:#ffffff;
}
*{margin:0;padding:0;box-sizing:border-box}
html,body{width:754px;height:1200px;overflow:hidden}
body{font-family:"Open Sans",Arial,sans-serif;background:var(--white);position:relative;color:var(--text)}
.abs{position:absolute}

/* header */
.site-header{left:0;top:0;width:754px;height:65px;background:var(--white)}
.header-left{left:0;top:0;width:260px;height:65px;background:#f6f6f6}
.brand{display:flex;align-items:center;gap:7px;left:52px;top:20px;font-size:19px;color:var(--ink);font-weight:400}
.brand-dot{width:22px;height:22px;border-radius:50%;background:var(--blue)}
.nav-tab{left:210px;top:0}
.nav-item{top:28px;font-size:8px;color:var(--ink);font-weight:600}
.nav-item.active{color:var(--white)}
.nav-sep{top:28px;font-size:8px;color:var(--blue)}

/* hero */
.hero{left:0;top:65px;width:754px;height:369px;background:linear-gradient(180deg,#dfe7ee 0%,#c7d2dc 40%,#b9c4cf 65%,#e6e9ee 100%)}
.hero-caption{left:50px;top:243px;width:260px;height:65px;background:rgba(60,70,85,.75);border-radius:3px;padding:12px 0 0 25px}
.hero-title{font-size:21px;color:var(--white);line-height:1.1}
.hero-sub{font-size:13px;color:var(--blue);margin-top:2px;padding-left:2px}
.slider-dots{left:336px;top:414px;display:flex;gap:10px}
.slider-dots span{width:8px;height:8px;border-radius:50%;border:1.5px solid var(--white)}
.slider-dots span.on{background:var(--blue);border-color:var(--blue)}

/* intro band */
.intro{left:0;top:434px;width:754px;height:114px;background:var(--blue)}
.intro-name{right:530px;top:40px;text-align:right;font-size:14px;font-weight:700;color:var(--white);line-height:17px;letter-spacing:.5px}
.intro-rule{left:258px;top:39px;width:2px;height:36px;background:var(--white)}
.intro-text{left:294px;top:35px;width:410px;font-size:8.6px;font-style:italic;color:var(--white);line-height:15px}
.intro-text a{color:var(--maroon);text-decoration:none}

/* services */
.card-img{top:573px;width:204px;height:140px;border:2px solid #eceef0}
.card-title{top:730px;font-size:12px;font-weight:700;color:var(--ink)}
.rule{height:2px;width:36px;background:var(--blue)}
.card-text{top:765px;width:204px;font-size:7.6px;line-height:15px;color:var(--text)}
.btn{height:24px;width:80px;background:var(--blue);color:var(--white);font-size:8px;font-weight:600;display:flex;align-items:center;justify-content:center}

/* lower section */
.lower{left:0;top:859px;width:754px;height:277px;background:var(--soft)}
.sec-title{font-size:15px;font-weight:700;color:var(--maroon-title)}
.founder-img{left:50px;top:919px;width:243px;height:104px;background:linear-gradient(135deg,#3b2f5a,#5a3a5e 45%,#c66a3a 60%,#3a3450)}
.founder-text{left:50px;top:1031px;width:245px;font-size:7.6px;line-height:14px;color:var(--text)}
.tabs{left:320px;top:918px;width:385px;height:25px;display:flex;background:var(--white);border:1px solid #dde1e5}
.tab{display:flex;align-items:center;justify-content:center;font-size:10px;color:var(--ink);border-right:1px solid #dde1e5;position:relative}
.tab.on{background:var(--blue);color:var(--white)}
.tab.on::after{content:"";position:absolute;bottom:-1px;left:50%;margin-left:-4px;border:4px solid transparent;border-bottom-color:var(--white)}
.values-head{left:323px;top:959px;font-size:10px;font-weight:600;color:var(--ink)}
.values-text{left:323px;top:986px;width:382px;font-size:7.6px;line-height:14px;color:var(--text)}
.value-list{list-style:none;top:1052px;font-size:8.4px;color:var(--ink)}
.value-list li{display:flex;align-items:center;gap:6px;height:19.5px}
.value-list svg{flex:none}

/* footer */
.site-footer{left:0;top:1136px;width:754px;height:64px;background:var(--maroon)}
.footer-brand{left:52px;top:1156px;display:flex;align-items:center;gap:7px;font-size:18px;color:var(--white)}
.footer-brand .brand-dot{background:var(--white)}
.copyright{left:254px;top:1163px;font-size:7.4px;color:var(--white)}
.copyright a{color:#6fc3e6;text-decoration:none}
.social{left:602px;top:1164px;display:flex;gap:13px}
.social span{width:9px;height:9px;border-radius:50%;background:var(--white)}
</style>
</head>
<body>

<header class="abs site-header">
  <div class="abs header-left"></div>
  <div class="abs brand"><span class="brand-dot"></span>Quillbrookes</div>
  <svg class="abs nav-tab" width="125" height="65" viewBox="0 0 125 65">
    <path d="M42 0 H120 Q108 50 66 65 H6 Q32 48 42 0 Z" fill="#3aa3cf"/>
  </svg>
  <span class="abs nav-item active" style="left:263px">Founder</span>
  <span class="abs nav-item" style="left:358px">Consultancy</span>
  <span class="abs nav-sep" style="left:436px">/</span>
  <span class="abs nav-item" style="left:469px">System</span>
  <span class="abs nav-sep" style="left:527px">/</span>
  <span class="abs nav-item" style="left:560px">Case Studies</span>
  <span class="abs nav-sep" style="left:639px">/</span>
  <span class="abs nav-item" style="left:673px">Contact</span>
</header>

<section class="abs hero" role="img" aria-label="Photo of business people meeting in a bright office with charts and a pen on the desk"></section>
<div class="abs hero-caption">
  <div class="hero-title">World Merchandising</div>
  <div class="hero-sub">Trade 2012 ( USD Billion)</div>
</div>
<div class="abs slider-dots"><span></span><span></span><span class="on"></span><span></span><span></span></div>

<section class="abs intro">
  <h2 class="abs intro-name">QUILLBROOKES<br>CONSULTANCY LIMITED</h2>
  <div class="abs intro-rule"></div>
  <p class="abs intro-text">Quillbrookes Consultancy Limited capitalizes on synergies arising from trade and investment linkages between countries and knowledge of traditional and non-traditional pools of liquidity to provide consultancy services to Emerging country banks, Corporates and SMEs... <a>Read more »</a></p>
</section>

<div class="abs card-img" style="left:51px;background:linear-gradient(135deg,#e9eef3,#8ea6bf 50%,#2e4a6b)" role="img" aria-label="Photo of a glass office tower"></div>
<div class="abs card-img" style="left:275px;background:linear-gradient(135deg,#8b96a3,#d9dde1 50%,#6f7a86)" role="img" aria-label="Photo of hands pointing at a tablet in a meeting"></div>
<div class="abs card-img" style="left:498px;background:linear-gradient(180deg,#e4e6e8,#9fa5ab 50%,#4a4f55)" role="img" aria-label="Photo of a calculator, pen and open book"></div>

<h3 class="abs card-title" style="left:52px">Our Expertise</h3>
<div class="abs rule" style="left:52px;top:754px"></div>
<p class="abs card-text" style="left:53px">QCL will work with you to understand your business and offer need based strategic and transactional</p>
<div class="abs btn" style="left:54px;top:809px">Read More »</div>

<h3 class="abs card-title" style="left:275px">Plain Vanilla Financing Solutions</h3>
<div class="abs rule" style="left:276px;top:754px"></div>
<p class="abs card-text" style="left:277px;top:766px">The Consultancy provides access to local/regional banks across Hong Kong, Singapore, Dubai , New York</p>
<div class="abs btn" style="left:277px;top:809px">Read More »</div>

<h3 class="abs card-title" style="left:501px;top:731px">Structured Financing Solutions</h3>
<div class="abs rule" style="left:501px;top:755px"></div>
<p class="abs card-text" style="left:502px;top:766px">The Consultancy provides end-to-end structured solutions on the Payables, Receivables or Inventory</p>
<div class="abs btn" style="left:502px;top:809px">Read More »</div>

<section class="abs lower"></section>
<h2 class="abs sec-title" style="left:52px;top:882px">Founder</h2>
<div class="abs rule" style="left:52px;top:908px"></div>
<div class="abs founder-img" role="img" aria-label="Photo of the founder speaking at a podium decorated with flowers"></div>
<p class="abs founder-text">Lorem ipsum dolor sit amet, consectetur adipiscing elit. Donec sed tellus quam. Proin est nibh, facilisis et nisi molestie, sagittis fringilla neque. Vivamus tempus, nibh tempus commodo convallis</p>
<div class="abs btn" style="left:51px;top:1080px">Read More »</div>

<h2 class="abs sec-title" style="left:320px;top:882px">Our Company Values</h2>
<div class="abs rule" style="left:320px;top:908px"></div>
<div class="abs tabs">
  <div class="tab on" style="width:118px">Quality</div>
  <div class="tab" style="width:144px">Case Studies</div>
  <div class="tab" style="width:121px;border-right:0">Success</div>
</div>
<h4 class="abs values-head">Quality</h4>
<p class="abs values-text">Lorem ipsum dolor sit amet, consectetur adipiscing elit. Donec sed tellus quam. Proin est nibh, facilisis et nisi molestie, sagittis fringilla neque. Vivamus tempus, nibh tempus commodo convallis, elit elit consectetur dui, vitae placerat risus odio id metus. Sed consectetur ipsum non libero suscipit.</p>
<ul class="abs value-list" style="left:326px">
  <li><svg width="7" height="7" viewBox="0 0 8 8"><circle cx="4" cy="4" r="4" fill="#3aa3cf"/><path d="M3 2 L5 4 L3 6" stroke="#fff" stroke-width="1.2" fill="none"/></svg>Our Company Growth</li>
  <li><svg width="7" height="7" viewBox="0 0 8 8"><circle cx="4" cy="4" r="4" fill="#3aa3cf"/><path d="M3 2 L5 4 L3 6" stroke="#fff" stroke-width="1.2" fill="none"/></svg>1000 Employed</li>
  <li><svg width="7" height="7" viewBox="0 0 8 8"><circle cx="4" cy="4" r="4" fill="#3aa3cf"/><path d="M3 2 L5 4 L3 6" stroke="#fff" stroke-width="1.2" fill="none"/></svg>Customer Relationship</li>
</ul>
<ul class="abs value-list" style="left:471px">
  <li><svg width="7" height="7" viewBox="0 0 8 8"><circle cx="4" cy="4" r="4" fill="#3aa3cf"/><path d="M3 2 L5 4 L3 6" stroke="#fff" stroke-width="1.2" fill="none"/></svg>Our Company Growth</li>
  <li><svg width="7" height="7" viewBox="0 0 8 8"><circle cx="4" cy="4" r="4" fill="#3aa3cf"/><path d="M3 2 L5 4 L3 6" stroke="#fff" stroke-width="1.2" fill="none"/></svg>1000 Employed</li>
  <li><svg width="7" height="7" viewBox="0 0 8 8"><circle cx="4" cy="4" r="4" fill="#3aa3cf"/><path d="M3 2 L5 4 L3 6" stroke="#fff" stroke-width="1.2" fill="none"/></svg>Customer Relationship</li>
</ul>

<footer class="abs site-footer"></footer>
<div class="abs footer-brand"><span class="brand-dot"></span>Quillbrookes</div>
<p class="abs copyright">QUILL-BROOKES © 2016 All Rights Reserved. <a>Terms of use</a> and <a>Privacy Policy</a></p>
<div class="abs social"><span></span><span></span><span></span><span></span><span></span></div>

</body>
</html>
```